Velmora Systems Website

Website design for our company: Velmora Systems.
The website should look fresh and IT focused. Please have a look at http://www.velmorasystems.example.au/ for our current design. We want something fresh and new, professional looking, in WordPress so we can easily make changes.

It Company

```html
<!DOCTYPE html>
<html lang="en">
<head>
<meta charset="utf-8">
<title>Velmora Systems</title>
<link href="https://fonts.googleapis.com/css2?family=Roboto:wght@300;400;500&family=Roboto+Condensed:wght@400;700&family=Open+Sans:wght@400;600&display=swap" rel="stylesheet">
<style>
:root{
  --green:#7a9a3f;
  --accent:#5ea600;
  --accent-dark:#3f8a00;
  --accent-text:#5ca30a;
  --text:#7a7a7a;
  --border:#d8d8d8;
  --menu-bg:#ececec;
  --white:#fff;
}
*{margin:0;padding:0;box-sizing:border-box}
html,body{width:1200px;height:1177px;overflow:hidden;background:var(--white);font-family:"Roboto",sans-serif}
.page{position:relative;width:1200px;height:1177px}
.abs{position:absolute}
.header{left:0;top:0;width:1200px;height:129px;background:var(--green)}
.brand{left:173px;top:24px;width:160px;height:82px;background:var(--white);border:3px solid var(--accent);border-radius:4px;display:flex;align-items:center;justify-content:center;gap:8px}
.brand-mark{width:14px;height:14px;background:var(--accent)}
.brand-name{font-family:"Open Sans",sans-serif;font-weight:600;font-size:16px;color:var(--accent-dark)}
.topline{right:171px;top:19px;display:flex;align-items:center;gap:9px;color:var(--white)}
.phone{font-family:"Open Sans",sans-serif;font-weight:600;font-size:15px;display:flex;align-items:center;gap:7px;margin-right:12px;color:#222}
.follow{font-family:"Open Sans",sans-serif;font-weight:600;font-size:17px;margin-right:4px}
.social{width:27px;height:27px;border:2px solid #222;border-radius:50%}
.nav{left:377px;top:59px;width:651px;height:46px;background:var(--white);border:2px solid #eaeaea;display:flex;align-items:center;justify-content:space-between;padding-right:14px;font-size:12.5px;color:#444}
.nav a{text-decoration:none;color:inherit;height:100%;display:flex;align-items:center}
.nav a.active{background:linear-gradient(#7ab33b,#6aa730);color:#fff;padding:0 17px;margin-left:-2px}
.box{border:1px solid var(--border);border-radius:4px;background:#fff;box-shadow:0 1px 2px rgba(0,0,0,.08)}
.hero{left:171px;top:150px;width:858px;height:386px}
.hero-photo{left:0;top:0;width:326px;height:384px;background:linear-gradient(90deg,#c9d6df 0%,#e6ecef 60%,#fff 100%);border-radius:4px 0 0 4px}
.welcome-icon{left:327px;top:30px;width:48px;height:40px;border-radius:50%;background:#3a6c8a;opacity:.8}
.h-title{font-family:"Roboto Condensed",sans-serif;font-weight:700;color:var(--accent-text)}
.welcome-title{left:381px;top:38px;font-size:27px}
.welcome-text{left:333px;top:91px;width:250px;font-size:13.6px;font-weight:300;line-height:18.9px;color:var(--text)}
.welcome-text p+p{margin-top:19px}
.btn{background:linear-gradient(#67b21b,#3f8d00);color:#fff;font-size:13px;display:flex;align-items:center;justify-content:center;border-radius:2px;text-decoration:none}
.learn{left:334px;top:304px;width:125px;height:27px;font-size:14px}
.menu{left:592px;top:52px;width:266px}
.menu-item{height:54px;background:var(--menu-bg);border-bottom:1px solid #d0d0d0;border-left:1px solid #d0d0d0;display:flex;align-items:center;padding-left:14px;gap:13px;font-size:19px;color:var(--accent-text)}
.menu-item .ic{width:36px;height:36px;border-radius:50%}
.menu-item.active{background:linear-gradient(#6fb31c,#3f8d00);color:#fff;width:285px;position:relative}
.menu-item.active::after{content:"";position:absolute;right:0;bottom:-18px;border-top:18px solid #356f00;border-left:19px solid transparent}
.strip{left:171px;width:858px;height:135px}
.arrow{width:34px;height:34px;border-radius:50%;background:radial-gradient(#888,#555);display:flex;align-items:center;justify-content:center}
.card{width:139px;height:99px;border:1px solid var(--border);background:#fff;box-shadow:0 8px 6px -6px rgba(0,0,0,.25);display:flex;flex-direction:column;align-items:center;padding-top:16px;gap:12px}
.card .ic{width:42px;height:40px;border-radius:6px}
.card span{font-family:"Roboto Condensed",sans-serif;font-size:16px;color:var(--accent-text)}
.svc-title{left:394px;top:726px;font-size:19px;font-weight:400}
.svc-text{left:394px;top:750px;width:560px;font-size:12.2px;line-height:15.5px;color:var(--text)}
.footer{left:0;top:858px;width:1200px;height:278px;background:var(--green);color:#fff}
.f-col{top:40px}
.f-col h3{font-family:"Open Sans",sans-serif;font-weight:600;font-size:17px;margin-bottom:12px;letter-spacing:-.2px}
.f-col li{list-style:none;font-size:11.5px;line-height:20.6px;letter-spacing:-.3px}
.field{background:#fff;color:#999;font-size:12px;padding-left:13px;display:flex;align-items:center}
.bottom{left:0;top:1136px;width:1200px;height:41px;background:var(--green);border-top:1px solid #6d8c33;color:#fff;font-size:11.5px;display:flex;align-items:center;justify-content:center}
</style>
</head>
<body>
<div class="page">
  <header class="header abs">
    <div class="brand abs"><span class="brand-mark"></span><span class="brand-name">Velmora Systems</span></div>
    <div class="topline abs">
      <span class="phone"><svg width="15" height="15" viewBox="0 0 24 24"><path fill="#fff" d="M6.6 10.8a15 15 0 0 0 6.6 6.6l2.2-2.2c.3-.3.7-.4 1-.2 1.1.4 2.3.6 3.6.6.6 0 1 .4 1 1V20c0 .6-.4 1-1 1A17 17 0 0 1 3 4c0-.6.4-1 1-1h3.5c.6 0 1 .4 1 1 0 1.3.2 2.5.6 3.6.1.3 0 .7-.2 1z"/></svg>555-0142-880</span>
      <span class="follow">FOLLOW US</span>
      <span class="social" role="img" aria-label="Social profile"></span>
      <span class="social" role="img" aria-label="Social profile"></span>
      <span class="social" role="img" aria-label="Social profile"></span>
    </div>
    <nav class="nav abs">
      <a class="active">HOME</a><a>SUPPLIERS</a><a>SERVICES</a><a>SUPPORTS</a><a>TESTIMONIALS</a><a>CONTACT US</a><a>ABOUT US</a>
    </nav>
  </header>

  <section class="hero box abs">
    <div class="hero-photo abs" role="img" aria-label="Photo of a smiling consultant at a computer desk"></div>
    <div class="welcome-icon abs" role="img" aria-label="Handshake icon"></div>
    <h1 class="h-title welcome-title abs">Welcome</h1>
    <div class="welcome-text abs">
      <p>We provide a high level of consulting services using the most experienced engineers at a reasonable and fair price. We believe in using a Business Value approach to every aspect of com-puter consulting to provide our clients with the most cost effective solutions.</p>
      <p>We strongly believe that we are in busi-ness with our clients.</p>
    </div>
    <a class="btn learn abs">Learn More</a>
    <div class="menu abs">
      <div class="menu-item active"><span class="ic" style="background:#2f5f7d" role="img" aria-label="Handshake icon"></span>Welcome</div>
      <div class="menu-item"><span class="ic" style="background:#7fb5df" role="img" aria-label="Globe icon"></span>Website Development</div>
      <div class="menu-item"><span class="ic" style="background:#6c89a8" role="img" aria-label="Gear icon"></span>Business</div>
      <div class="menu-item"><span class="ic" style="background:#3d8fd1" role="img" aria-label="Design icon"></span>Web Design</div>
      <div class="menu-item"><span class="ic" style="background:#c24a3c" role="img" aria-label="Tools icon"></span>Computer Repair</div>
    </div>
  </section>

  <section class="strip box abs" style="top:553px">
    <div class="arrow abs" style="left:14px;top:50px"><svg width="8" height="10"><path d="M7 0v10L0 5z" fill="#222"/></svg></div>
    <div class="card abs" style="left:62px;top:16px"><span class="ic" style="background:#4a8fcf" role="img" aria-label="Web design icon"></span><span>Web Design</span></div>
    <div class="card abs" style="left:210px;top:16px"><span class="ic" style="background:#8fc3e8" role="img" aria-label="Globe icon"></span><span>Web Development</span></div>
    <div class="card abs" style="left:358px;top:16px"><span class="ic" style="background:#8a949c" role="img" aria-label="Monitor icon"></span><span>Web Increase</span></div>
    <div class="card abs" style="left:506px;top:16px"><span class="ic" style="background:#b8b8b8" role="img" aria-label="SEO icon"></span><span>Web Seo</span></div>
    <div class="card abs" style="left:654px;top:16px"><span class="ic" style="background:#7cc12e" role="img" aria-label="Mobile app icon"></span><span>Mobile Apps</span></div>
    <div class="arrow abs" style="left:808px;top:50px"><svg width="8" height="10"><path d="M1 0v10l7-5z" fill="#222"/></svg></div>
  </section>

  <section class="strip box abs" style="top:705px">
    <div class="arrow abs" style="left:14px;top:50px"><svg width="8" height="10"><path d="M7 0v10L0 5z" fill="#222"/></svg></div>
    <div class="card abs" style="left:62px;top:16px"><span class="ic" style="background:#3f78b8" role="img" aria-label="Computer service icon"></span><span>Services</span></div>
    <div class="arrow abs" style="left:808px;top:50px"><svg width="8" height="10"><path d="M1 0v10l7-5z" fill="#222"/></svg></div>
  </section>
  <h2 class="h-title svc-title abs">Services</h2>
  <p class="svc-text abs">We specialise in building, installing and managing customised servers for businesses of all sizes. Servers can be managed at your premises or ours.Data is stored at a central point on the server, this allows the business to control the data and set certain access restriction policies. The firewall on the server also adds security to protect your data from unauthorised access.</p>

  <footer class="footer abs">
    <div class="f-col abs" style="left:171px"><h3>LOCATION</h3><ul>
      <li>27 Harbour Lane</li><li>Kestrel Bay</li><li>5099 Australia</li><li>Phone:0855501234</li><li>Fax:085550 9876</li><li>Mobile:0855501234</li><li>E-mail : hello@velmorasystems.example.au</li></ul></div>
    <div class="f-col abs" style="left:344px"><h3>COMPUTER REPAIR</h3><ul>
      <li>About Computer Repair</li><li>Drop-Off Computer Repair</li><li>In-Home Computer Support</li><li>Virus Removal</li><li>System Support</li></ul></div>
    <div class="f-col abs" style="left:530px"><h3>WEB DESIGN</h3><ul>
      <li>About Web Design</li><li>Design Portfolio</li><li>Free Web Design Consultation</li><li>The Four Elements of a Website</li><li>Web Design Pricing</li></ul></div>
    <div class="f-col abs" style="left:704px"><h3>CONTACT US</h3></div>
    <div class="field abs" style="left:704px;top:67px;width:150px;height:31px">Name</div>
    <div class="field abs" style="left:704px;top:106px;width:150px;height:31px">E-mail</div>
    <div class="field abs" style="left:704px;top:146px;width:150px;height:60px;align-items:flex-start;padding-top:9px">Message</div>
    <a class="btn abs" style="left:704px;top:217px;width:74px;height:33px">Send</a>
    <div class="f-col abs" style="left:871px"><h3>REMOTE SUPPORT</h3></div>
    <p class="abs" style="left:871px;top:71px;font-size:12.5px">Enter your 6-digit code</p>
    <div class="field abs" style="left:872px;top:92px;width:156px;height:31px;color:#aaa">Enter your 6-digit code</div>
    <a class="btn abs" style="left:872px;top:134px;width:117px;height:33px">Connect Now</a>
  </footer>
  <div class="bottom abs">© 2014 Velmora Systems&nbsp; All Rights Reserved.</div>
</div>
</body>
</html>
```